Business card design for a dynamic IT consulting company

We need a business card design for a young firm, specialized in the Telecommunications/Consulting industry. The name of the company is Quindor and Partners Business Consulting Ltd. (Short name: Quindor and Partnes)
Quindor = solve read reverse, so we aim to be uncomplicated and solution-oriented. The small pipe in our logo is also related to the word solve. So we need a new business card design, which is simple, eye catching and something non traditional (I would probably prefer a square shaped design rather than a rectangle, but open for suggestions). Attached our logo.

Target Market(s)

Usually our customers are Tier1 Telecoms providers (Q-Netra, Palorix, etc) and their executives.

Industry/Entity Type

Business

Contact Information for Business Card

Name: Bence Tolnavari
Email: b.tolnavari@quindor.hu
Web: www.quindor.hu
Mobile: +36 30 518 2769
Title: Managing Director

Optional:
Company name: Quindor and Partners Ltd.
Address: 1087 Budapest, Tolvenka str. 28/C, Hungary

Font styles to use
Other font styles liked:
• helveticaneue_medium, Prime Regular are used now.

Colors

Designer to choose colors to be used in the design.

Requirements
Must have
• I would like to have a 2 sided design.
Nice to have
• I thought if we make the logo a bit bigger (without the company name), that could go to the back with the company name below. I though, if the pipe in the logo is somehow touchable on the business card, would be nice and unique.

```html
<!DOCTYPE html>
<html lang="en">
<head>
<meta charset="utf-8">
<title>Quindor &amp; Partners – Business Card</title>
<link rel="stylesheet" href="https://fonts.googleapis.com/css2?family=Bebas+Neue&family=Exo+2:wght@400;500&family=Work+Sans:wght@400;500&display=swap">
<style>
  :root {
    --page: #161616;
    --card: #262626;
    --card-light: #2f2f2f;
    --ink: #f2f2f2;
    --blue: #1e9bd7;
    --magenta: #c0237a;
  }
  * { margin: 0; padding: 0; box-sizing: border-box; }
  html, body {
    width: 1200px; height: 897px; overflow: hidden;
    background: var(--page);
  }
  .canvas { position: relative; width: 1200px; height: 897px; }
  .card {
    position: absolute; left: 304px; width: 594px; height: 338px;
    border-radius: 16px;
    background: linear-gradient(135deg, var(--card) 40%, var(--card-light) 75%, var(--card) 100%);
    color: var(--ink);
  }
  .card--front { top: 92px; }
  .card--back { top: 469px; }

  .wordmark {
    position: absolute; left: 0; right: 0;
    display: flex; align-items: center; justify-content: center; gap: 12px;
    font-family: "Exo 2", sans-serif; font-weight: 400; color: var(--ink);
    white-space: nowrap;
  }
  .wordmark__square { background: var(--magenta); flex: none; }
  .card--front .wordmark { top: 42px; font-size: 38px; }
  .card--front .wordmark__square { width: 14px; height: 14px; }
  .card--back .wordmark { top: 136px; font-size: 50px; }
  .card--back .wordmark__square { width: 18px; height: 18px; }

  .person {
    position: absolute; right: 292px; top: 164px; text-align: right;
  }
  .person__name {
    font-family: "Bebas Neue", sans-serif; font-size: 36px; line-height: 1;
    color: var(--blue); letter-spacing: 0.3px; white-space: nowrap;
  }
  .person__title {
    margin-top: 6px;
    font-family: "Work Sans", sans-serif; font-size: 14px; letter-spacing: 0.4px;
    white-space: nowrap;
  }
  .divider {
    position: absolute; left: 326px; top: 164px; width: 2px; height: 56px;
    background: var(--magenta);
  }
  .contacts {
    position: absolute; left: 350px; top: 166px; list-style: none;
    font-family: "Work Sans", sans-serif; font-size: 13.5px; letter-spacing: 0.3px;
  }
  .contacts li { display: flex; align-items: center; height: 19px; gap: 12px; white-space: nowrap; }
  .contacts svg { width: 11px; height: 11px; flex: none; }

  .company {
    position: absolute; left: 0; right: 0; top: 280px; text-align: center;
  }
  .company__name {
    font-family: "Exo 2", sans-serif; font-weight: 500; font-size: 15px;
    color: var(--blue); letter-spacing: 0.3px;
  }
  .company__address {
    margin-top: 2px;
    font-family: "Work Sans", sans-serif; font-size: 13.5px; letter-spacing: 0.6px;
  }
  .back__web {
    position: absolute; left: 0; right: 0; top: 296px; text-align: center;
    font-family: "Work Sans", sans-serif; font-size: 15.5px; letter-spacing: 2.5px;
  }
</style>
</head>
<body>
<main class="canvas">

  <section class="card card--front" aria-label="Card front">
    <div class="wordmark"><span class="wordmark__square"></span><span>Quindor &amp; Partners</span></div>

    <div class="person">
      <p class="person__name">BENCE TOLNAVARI</p>
      <p class="person__title">MANAGING DIRECTOR</p>
    </div>
    <div class="divider"></div>
    <ul class="contacts">
      <li>
        <svg viewBox="0 0 12 12" aria-hidden="true"><path fill="#1e9bd7" d="M2.4 0.6 L4.2 0.6 L5 3.2 L3.7 4.2 C4.4 5.8 6.2 7.6 7.8 8.3 L8.8 7 L11.4 7.8 L11.4 9.6 C11.4 10.6 10.6 11.4 9.6 11.4 C5 11.1 0.9 7 0.6 2.4 C0.6 1.4 1.4 0.6 2.4 0.6 Z"/></svg>
        <span>+36 30 518 2769</span>
      </li>
      <li>
        <svg viewBox="0 0 12 12" aria-hidden="true"><rect x="0.5" y="2" width="11" height="8" fill="#1e9bd7"/><path d="M0.5 2 L6 6.5 L11.5 2" fill="none" stroke="#262626" stroke-width="1"/></svg>
        <span>b.tolnavari@quindor.hu</span>
      </li>
      <li>
        <svg viewBox="0 0 12 12" aria-hidden="true"><g fill="none" stroke="#1e9bd7" stroke-width="1"><circle cx="6" cy="6" r="5.2"/><ellipse cx="6" cy="6" rx="2.3" ry="5.2"/><path d="M0.8 6 H11.2 M1.6 3.4 H10.4 M1.6 8.6 H10.4"/></g></svg>
        <span>www.quindor.hu</span>
      </li>
    </ul>

    <div class="company">
      <p class="company__name">QUINDOR AND PARTNERS LTD:</p>
      <p class="company__address">1087 Budapest, Tolvenka str. 28/C, Hungary</p>
    </div>
  </section>

  <section class="card card--back" aria-label="Card back">
    <div class="wordmark"><span class="wordmark__square"></span><span>Quindor &amp; Partners</span></div>
    <p class="back__web">www.quindor.hu</p>
  </section>

</main>
</body>
</html>
```